skincare creams for tired moms

I need a package and a logo design for a skincare company based in California called Petal Ledger. I make day and night cream, under eye cream, and body lotion. The first product I plan to launch is an under eye cream. It does not have to be in these colors but I do teals, greens, black, and cobalt blue.

The package is going to either be in a box or a bag. Either way I go it will be like a gift box or bag. The design should make the person feel like they are getting something special and luxurious just for them.
Updates

I have small kids and it is really difficult to find a chunk of time to myself to update or review.

Need extra days to review

Target Market(s)

mainly first time moms. I am making an under eye cream that does not use retinol but is still powerful enough to get rid of bags and dark circles.

Industry/Entity Type

Cosmetics

Logo Text

The package and logo should incorporate the name Petal Ledger.

Font styles to use
Decorative
Script

Colors

Designer to choose colors to be used in the design.

Requirements
Nice to have
• maybe focus more on Ledger instead of Petal. Also incorporate plants or flowers
Should not have
• not a huge fan of pink

```html
<!DOCTYPE html>
<html lang="en">
<head>
<meta charset="UTF-8">
<title>Petal Ledger Eye Cream Label</title>
<link href="https://fonts.googleapis.com/css2?family=Raleway:wght@300;400&family=Montserrat:wght@400;500&display=swap" rel="stylesheet">
<style>
  :root {
    --backdrop: #eeeeee;
    --label-white: #f3f2f0;
    --label-blue: #c4dff2;
    --ink: #1f2a45;
  }
  html, body {
    margin: 0;
    padding: 0;
    width: 900px;
    height: 1200px;
    overflow: hidden;
    background: var(--backdrop);
  }
  .canvas {
    position: relative;
    width: 900px;
    height: 1200px;
    display: flex;
    align-items: center;
    justify-content: center;
  }
  .label {
    width: 600px;
    height: 1100px;
    display: flex;
    flex-direction: column;
    box-shadow: 0 2px 10px rgba(0,0,0,0.08);
  }
  .label-top {
    flex: 0 0 555px;
    background: var(--label-white);
    display: flex;
    flex-direction: column;
    align-items: center;
    justify-content: flex-end;
    padding-bottom: 150px;
    box-sizing: border-box;
  }
  .brand {
    text-align: center;
    color: var(--ink);
    font-family: 'Raleway', sans-serif;
    font-weight: 300;
  }
  .brand-first {
    display: block;
    font-size: 26px;
    letter-spacing: 14px;
    margin-left: 14px;
    margin-bottom: 2px;
  }
  .brand-second {
    display: block;
    font-size: 78px;
    letter-spacing: 1px;
    line-height: 1;
  }
  .label-band {
    flex: 1;
    background: var(--label-blue);
    padding: 40px 0 0 96px;
    box-sizing: border-box;
    color: var(--ink);
    font-family: 'Montserrat', sans-serif;
  }
  .product-name {
    font-size: 50px;
    font-weight: 400;
    letter-spacing: 1px;
    margin: 0;
    line-height: 1;
  }
  .product-name .accent {
    display: inline-block;
    border-left: 2px solid var(--ink);
    border-bottom: 2px solid var(--ink);
    padding: 0 8px 4px 6px;
    margin-right: 4px;
  }
  .ingredients {
    display: inline-block;
    margin-top: 30px;
    border-left: 2px solid var(--ink);
    border-top: 2px solid var(--ink);
    padding: 6px 10px 4px 8px;
    font-size: 27px;
    line-height: 1.3;
    letter-spacing: 0.5px;
    text-transform: uppercase;
  }
  .volume {
    margin-top: 52px;
    font-size: 27px;
    margin-left: 40px;
  }
</style>
</head>
<body>
  <main class="canvas">
    <section class="label">
      <div class="label-top">
        <div class="brand">
          <span class="brand-first">PETAL</span>
          <span class="brand-second">LEDGER</span>
        </div>
      </div>
      <div class="label-band">
        <h1 class="product-name"><span class="accent">EYE</span>CREAM</h1>
        <div class="ingredients">Hyaluronic Acid<br>Collagen, Caffeine</div>
        <div class="volume">0.5 oz / 15 ml</div>
      </div>
    </section>
  </main>
</body>
</html>
```